Wordpress website for a new Podcast

Hi, We are looking for a designer to create a wordpress website project for a new podcast and publish it on the domain we own.

The show is called “Bright Gatherings” (logo included) and its aim is to interview guests who work as professional facilitators, trainers, teachers and coaches. The show has a positive vibe, is fun, vibrant and full of positive energy. These are the feelings we want to convey in the design.

The website should have a similar structure to: https://www.plumvesselcast.example/ with the following content:

1) The main page including:
- navigation bar and social buttons at the top
- main graphic design featuring the latest episode
- "latest episodes" section displaying 3 episodes (please design a mask to be used for new episodes when they air together with the face of the interviewee) -> this will link to the respective episodes
- please design an "bright gatherings" book cover mockup to be inluded as a banner -> this will link to Orindel
- subscribe to the newsletter - a banner capturing the name and email of the user -> to be connected to PostWren.
-> a working episode search.

2) Episodes page
- the show will be divided into seasons (12 episodes each) and each episode will need a separate "blog entry" including:
-> A short article (4-5 paragraphs) + stock image
-> interviewee's bio and social links

3) Meet the hosts page
- including bios of the two hosts of the show
- links to their social profiles
- a "request speaker availability" form which sends an email

Some additional nice-to-haves:
1) Good and clean Bio's would be awesome (both for the hosts & the interviewees),
2) an easily navigable episode system,
3) a keyword/date search option
4) easy to share options (share to WhatsApp, Facebook, Twitter, LinkedIn) 5) We must be able to track how the podcasts are shared (google analytics?)

```html
<!DOCTYPE html>
<html lang="en">
<head>
<meta charset="utf-8">
<title>Bright Gatherings — Podcast</title>
<link rel="stylesheet" href="https://fonts.googleapis.com/css2?family=Josefin+Sans:wght@400;600;700&family=Montserrat:wght@400;500;600;700&display=swap">
<style>
:root{
  --red:#f2350c;
  --red-deep:#e02a06;
  --yellow:#f2d11a;
  --orange:#f6820f;
  --ink:#222222;
  --body:#444444;
  --grey:#ebebeb;
  --pink:#fbd9cf;
  --footer:#171717;
  --white:#ffffff;
}
*{box-sizing:border-box;margin:0;padding:0}
html,body{width:1200px;height:3311px;overflow:hidden;background:var(--white)}
body{font-family:"Montserrat",sans-serif;color:var(--body);position:relative}
.page{position:relative;width:1200px;height:3311px;overflow:hidden}
.abs{position:absolute}
a{text-decoration:none}
h1,h2,h3,h4{font-family:"Josefin Sans",sans-serif;color:var(--ink);font-weight:600}
.dots{position:absolute;display:flex;gap:5px}
.dots i{width:9px;height:9px;border-radius:50%;background:var(--red);display:block}
.btn{position:absolute;display:flex;align-items:center;justify-content:center;border-radius:20px;font-family:"Josefin Sans",sans-serif;font-weight:700;color:var(--white);background:var(--red)}

/* header */
.site-header{position:absolute;left:0;top:0;width:1200px;height:85px;background:var(--red);z-index:5}
.nav a{position:absolute;top:35px;color:var(--white);font-family:"Josefin Sans",sans-serif;font-weight:600;font-size:15px;letter-spacing:.5px}
.brand{position:absolute;left:538px;top:-6px;width:124px;height:126px;border-radius:50%;background:radial-gradient(circle at 50% 40%,var(--yellow),var(--orange) 55%,var(--red) 90%);display:flex;align-items:center;justify-content:center;text-align:center;z-index:6}
.brand span{font-family:"Josefin Sans",sans-serif;font-weight:700;font-size:16px;line-height:1.05;color:var(--ink);margin-top:-18px}
.search{position:absolute;left:726px;top:36px;width:150px;border-bottom:1px solid rgba(255,255,255,.8);color:var(--white);font-size:10px;padding-bottom:3px}
.social{position:absolute;left:930px;top:34px;display:flex;gap:10px}
.social i{display:block;width:16px;height:16px;border-radius:50%;background:var(--white)}

/* hero */
.hero{position:absolute;left:0;top:85px;width:1200px;height:610px;background:linear-gradient(120deg,#3a3633,#24201e 45%,#3b3430 75%,#2a2724)}
.book{position:absolute;left:225px;top:198px;width:268px;height:355px;transform:rotate(-1.5deg);background:linear-gradient(150deg,#ffffff 40%,#f7c1b2 60%,#e8492a 80%,#9b4a6c);box-shadow:6px 8px 18px rgba(0,0,0,.45)}
.hero-title{position:absolute;left:560px;top:270px;width:496px;text-align:center;color:var(--white);font-size:44px;font-weight:600}
.hero-text{position:absolute;left:585px;top:338px;width:446px;text-align:center;color:var(--white);font-size:12px;line-height:20px}
.arrow{position:absolute;top:348px}

/* about */
.about-title{position:absolute;left:173px;top:808px;font-size:28px}
.about-text{position:absolute;left:173px;top:875px;width:396px;font-size:10.4px;letter-spacing:-.1px;line-height:21.6px;text-align:justify}
.about-backdrop{position:absolute;left:745px;top:803px;width:322px;height:255px;background:var(--pink)}
.photo{background:linear-gradient(135deg,#dfe6ec,#b7c2cc 45%,#3b3f48 70%,#1f2228)}

/* podcast */
.section-title{position:absolute;left:0;width:1200px;text-align:center;font-size:28px}
.card{position:absolute;top:1516px;width:272px;height:419px;background:var(--white);border:1px solid #dddddd;text-align:center}
.card-photo{position:absolute;left:0;top:0;width:270px;height:184px}
.card-photo p{position:absolute;left:164px;top:46px;width:96px;text-align:left;color:var(--white);font-family:"Josefin Sans",sans-serif;font-weight:600;font-size:15px;line-height:21px}
.card-photo p b{font-size:19px}
.pod-icon{position:absolute;left:120px;top:170px;width:30px;height:30px;border-radius:50%;background:var(--red)}
.card .ep{position:absolute;left:0;top:209px;width:100%;font-size:9.5px}
.card h3{position:absolute;left:20px;top:230px;width:230px;font-size:16px;line-height:21px}
.card .desc{position:absolute;left:24px;top:282px;width:222px;font-size:10.5px;line-height:17px}

/* partners */
.partner{position:absolute;top:2260px;width:200px;text-align:center}
.partner .ring{position:absolute;left:10px;top:0;width:182px;height:172px;border-radius:50%;background:var(--pink)}
.partner .face{position:absolute;left:8px;top:0;width:176px;height:172px;border-radius:50%}
.partner h4{position:absolute;left:0;top:205px;width:100%;font-size:17px}
.partner p{position:absolute;left:0;top:233px;width:100%;font-size:11px;line-height:19.5px}

/* newsletter */
.footer{position:absolute;left:0;top:2887px;width:1200px;height:424px;background:var(--footer)}
.newsletter{position:absolute;left:172px;top:2682px;width:855px;height:296px;background:var(--grey);text-align:center}
.newsletter h2{position:absolute;left:0;top:56px;width:100%;font-size:34px}
.newsletter p{position:absolute;left:150px;top:134px;width:555px;font-size:11px;line-height:19px}
.field{position:absolute;top:190px;width:258px;height:40px;border-radius:20px;background:var(--white);border:1px solid #d6d6d6;font-size:11px;color:#555;padding:14px 14px;text-align:left}

/* footer */
.f-col{position:absolute;top:3036px}
.f-col h4{color:var(--white);font-size:15px;margin-bottom:18px}
.f-col ul{list-style:none}
.f-col li{color:#cfcfcf;font-size:11px;line-height:22.5px}
.contact-item{position:absolute;left:173px;display:flex;gap:14px;color:#cfcfcf;font-size:11px;line-height:19px}
.copyright{position:absolute;left:171px;top:3266px;color:#cfcfcf;font-size:12px}
</style>
</head>
<body>
<div class="page">

<header class="site-header">
  <nav class="nav">
    <a href="#" style="left:173px">HOME</a>
    <a href="#" style="left:249px">EPISODES</a>
    <a href="#" style="left:348px">MEET THE HOSTS</a>
  </nav>
  <div class="search">Keyword:</div>
  <svg class="abs" style="left:876px;top:34px" width="20" height="20" viewBox="0 0 20 20"><circle cx="8" cy="8" r="6" fill="none" stroke="#fff" stroke-width="2.5"/><line x1="12.5" y1="12.5" x2="18" y2="18" stroke="#fff" stroke-width="3" stroke-linecap="round"/></svg>
  <div class="social" aria-label="Share links"><i></i><i></i><i></i><i></i></div>
</header>
<a class="brand" href="#"><span>Bright<br>Gatherings</span></a>

<section class="hero" role="img" aria-label="Team meeting around a table, darkened background photo">
</section>
<div class="book" role="img" aria-label="Bright Gatherings book cover mockup"></div>
<svg class="arrow" style="left:38px" width="34" height="66" viewBox="0 0 34 66"><polyline points="32,2 2,33 32,64" fill="none" stroke="#fff" stroke-width="2"/></svg>
<svg class="arrow" style="left:1127px" width="34" height="66" viewBox="0 0 34 66"><polyline points="2,2 32,33 2,64" fill="none" stroke="#fff" stroke-width="2"/></svg>
<h1 class="hero-title">Bright Gatherings</h1>
<p class="hero-text">Sed ut perspiciatis unde omnis iste natus error sit voluptatem accusan tium dolore mque laudantium, totam rem aperiam, eaque ipsa quaeab illo inventorSed ut perspiciatis unde omnis iste natus error sit volupt</p>
<a class="btn" href="#" style="left:644px;top:432px;width:166px;height:43px;font-size:15px">Get the Book Now</a>
<a class="btn" href="#" style="left:825px;top:432px;width:127px;height:43px;font-size:15px;background:var(--yellow);color:var(--ink)">Get Trained</a>

<svg class="abs" style="left:0;top:600px" width="1200" height="110" viewBox="0 0 1200 110">
  <defs>
    <linearGradient id="arcGrad" x1="0" x2="1"><stop offset="0" stop-color="#f04a0c"/><stop offset=".5" stop-color="#f2d11a"/><stop offset="1" stop-color="#f04a0c"/></linearGradient>
  </defs>
  <path d="M0 35 Q600 115 1200 35 L1200 110 L0 110 Z" fill="#fff"/>
  <path d="M148 57 Q600 126 1052 57 Q600 108 148 57 Z" fill="url(#arcGrad)"/>
</svg>

<section>
  <h2 class="about-title">About Bright Gatherings</h2>
  <div class="dots" style="left:173px;top:855px"><i></i><i></i><i></i></div>
  <p class="about-text">Sed ut perspiciatis unde omnis iste natus error sit voluptatem accusantium doloremque laudantium, totam rem aperiam, eaque ipsa quae ab illo inventore veritatis et quasi architecto beatae vitae dicta sunt explicabo. Nemo enim ipsam voluptatem quia voluptas sit aspernatur aut odit aut fugit, sed quia consequuntur magni dolores eos qui ratione voluptatem sequi nesciunt. Neque porro quisquam est, qui doloSed ut perspiciatis unde omnis iste natus error sit voluptatem accusantium doloremque laudantium, totam rem aperiam, eaque ipsa quae ab illo inventore veritatis et quasi architecto beatae vitae dicta sunt explicaboemo enim ipsam voluptatem quia voluptas sit aspernatur aut odit aut fugit, sed quia consequuntur magni dolores eos qui ratione voluptatem</p>
  <a class="btn" href="#" style="left:173px;top:1127px;width:89px;height:29px;font-size:11px">Read More</a>
  <div class="about-backdrop"></div>
  <div class="abs photo" style="left:606px;top:841px;width:421px;height:306px" role="img" aria-label="Two businessmen talking at a laptop"></div>
</section>

<svg class="abs" style="left:0;top:1290px" width="1200" height="800" viewBox="0 0 1200 800">
  <defs>
    <linearGradient id="arcGrad2" x1="0" x2="1"><stop offset="0" stop-color="#f04a0c"/><stop offset=".5" stop-color="#f2d11a"/><stop offset="1" stop-color="#f04a0c"/></linearGradient>
  </defs>
  <path d="M0 68 Q600 -10 1200 68 L1200 745 Q600 820 0 745 Z" fill="#ebebeb"/>
  <path d="M205 45 Q600 -18 1010 45 Q600 2 205 45 Z" fill="url(#arcGrad2)"/>
  <path d="M295 775 Q600 812 900 775 Q600 830 295 775 Z" fill="url(#arcGrad2)"/>
</svg>

<section>
  <h2 class="section-title" style="top:1433px">Latest Podcast Episode</h2>
  <div class="dots" style="left:583px;top:1479px"><i></i><i></i><i></i></div>

  <article class="card" style="left:172px">
    <div class="card-photo photo" role="img" aria-label="Guest portrait for episode 195"><p>Sed ut pers piciatis unle <b>lonis iste</b> usit voluto atesa.</p></div>
    <span class="pod-icon"></span>
    <p class="ep">Episode 195:</p>
    <h3>Sed ut perspiciatis unlelonis iste natu sit voluptlo atesa.</h3>
    <p class="desc">Sed ut perspiciatis unde omnis iste natus error sit voluptatem accusantium dolore mque laudantium, totam rem aperiam, eaque ipsa quae ab illo inventora</p>
    <a class="btn" href="#" style="left:90px;top:368px;width:90px;height:29px;font-size:11px">Read More</a>
  </article>
  <article class="card" style="left:463px">
    <div class="card-photo photo" role="img" aria-label="Guest portrait for episode 196"><p>Sed ut pers piciatis unle <b>lonis iste</b> usit voluto atesa.</p></div>
    <span class="pod-icon"></span>
    <p class="ep">Episode 196:</p>
    <h3>Sed ut perspiciatis unlelonis iste natu sit voluptlo atesa.</h3>
    <p class="desc">Sed ut perspiciatis unde omnis iste natus error sit voluptatem accusantium dolore mque laudantium, totam rem aperiam, eaque ipsa quae ab illo inventora</p>
    <a class="btn" href="#" style="left:90px;top:368px;width:90px;height:29px;font-size:11px">Read More</a>
  </article>
  <article class="card" style="left:755px">
    <div class="card-photo photo" role="img" aria-label="Guest portrait for episode 197"><p>Sed ut pers piciatis unle <b>lonis iste</b> usit voluto atesa.</p></div>
    <span class="pod-icon"></span>
    <p class="ep">Episode 197:</p>
    <h3>Sed ut perspiciatis unlelonis iste natu sit voluptlo atesa.</h3>
    <p class="desc">Sed ut perspiciatis unde omnis iste natus error sit voluptatem accusantium dolore mque laudantium, totam rem aperiam, eaque ipsa quae ab illo inventora</p>
    <a class="btn" href="#" style="left:90px;top:368px;width:90px;height:29px;font-size:11px">Read More</a>
  </article>
</section>

<section>
  <h2 class="section-title" style="top:2178px">We Work With</h2>
  <div class="dots" style="left:583px;top:2224px"><i></i><i></i><i></i></div>

  <div class="partner" style="left:163px">
    <span class="ring"></span><span class="face photo" role="img" aria-label="Portrait of a facilitator"></span>
    <h4>Facilitators</h4>
    <p>Sed ut perspiciatis unde omnis iste natus error sit voluptatem acc usantium dolore mquedantium, totam rem aperiam, eaque ipsa quae ab illo inveed ut pe.</p>
  </div>
  <div class="partner" style="left:386px">
    <span class="ring"></span><span class="face photo" role="img" aria-label="Portrait of a trainer"></span>
    <h4>Trainers</h4>
    <p>Sed ut perspiciatis unde omnis iste natus error sit voluptatem acc usantium dolore mquedantium, totam rem aperiam, eaque ipsa quae ab illo inveed ut pe.</p>
  </div>
  <div class="partner" style="left:608px">
    <span class="ring"></span><span class="face photo" role="img" aria-label="Portrait of a teacher"></span>
    <h4>Teachers</h4>
    <p>Sed ut perspiciatis unde omnis iste natus error sit voluptatem acc usantium dolore mquedantium, totam rem aperiam, eaque ipsa quae ab illo inveed ut pe.</p>
  </div>
  <div class="partner" style="left:833px">
    <span class="ring"></span><span class="face photo" role="img" aria-label="Portrait of a coach"></span>
    <h4>Coaches</h4>
    <p>Sed ut perspiciatis unde omnis iste natus error sit voluptatem acc usantium dolore mquedantium, totam rem aperiam, eaque ipsa quae ab illo inveed ut pe.</p>
  </div>
</section>

<footer class="footer"></footer>

<section class="newsletter">
  <h2>Subscribe Newsletter</h2>
  <div class="dots" style="left:411px;top:106px"><i></i><i></i><i></i></div>
  <p>Sed ut perspiciatis unde omnis iste natus error sit voluptatem accusantium dolore mque laudantium, totam rem aperiam, eaque ipsa quae ab illo invSed ut perspiciatis unde omnis iste natus</p>
  <div class="field" style="left:118px">Name:</div>
  <div class="field" style="left:381px">Email:</div>
  <a class="btn" href="#" style="left:643px;top:190px;width:95px;height:40px;font-size:13px">Sign Up</a>
</section>

<div class="f-col" style="left:173px"><h4>Contact</h4></div>
<div class="contact-item" style="top:3073px">
  <svg width="18" height="22" viewBox="0 0 18 22"><path d="M9 1a7 7 0 0 1 7 7c0 5-7 13-7 13S2 13 2 8a7 7 0 0 1 7-7z" fill="none" stroke="#f2350c" stroke-width="1.6"/><circle cx="9" cy="8" r="2.5" fill="none" stroke="#f2350c" stroke-width="1.6"/></svg>
  <span>412 Lantern Row,<br>Fennick Vale</span>
</div>
<div class="contact-item" style="top:3125px">
  <svg width="22" height="22" viewBox="0 0 22 22"><path d="M5 2l4 4-2 3c1 3 3 5 6 6l3-2 4 4-3 3C9 20 2 13 2 5z" fill="none" stroke="#f2350c" stroke-width="1.5" stroke-linejoin="round"/></svg>
  <span>0 100 555 014 27<br>0 100 555 038 61</span>
</div>
<div class="contact-item" style="top:3178px">
  <svg width="22" height="18" viewBox="0 0 22 18"><rect x="1" y="2" width="20" height="14" fill="none" stroke="#f2350c" stroke-width="1.5"/><polyline points="1,2 11,10 21,2" fill="none" stroke="#f2350c" stroke-width="1.5"/></svg>
  <span>info@example.com<br>founder@example.com</span>
</div>

<div class="f-col" style="left:439px"><h4>Company</h4>
  <ul><li>Lorem ipsum dolo</li><li>Consectetur adipiscing elit.</li><li>Fusce eget leo tincid</li><li>Donec consequat</li><li>Praesent elementum</li><li>Jmauris posueret</li></ul>
</div>
<div class="f-col" style="left:669px"><h4>Information</h4>
  <ul><li>Lorem ipsum dolo</li><li>Consectetur adipiscing elit.</li><li>Fusce eec consequat</li><li>Praesent elementum</li><li>Jmauris posueret</li><li>Aenean a ex eu lectu</li></ul>
</div>
<div class="f-col" style="left:882px"><h4>Other Links</h4>
  <ul><li>Lorem ipsum dolo</li><li>Consecteturiscing elit.</li><li>Fusce eget leo tincid</li><li>Donec consequat</li><li>Praesent elementum</li><li>Aenean a ex eu lectu</li></ul>
</div>

<p class="copyright">Copyright 2019 Bright Gatherings. All Rights Reserved</p>
<a class="btn" href="#" style="left:922px;top:3258px;width:105px;height:32px;font-size:13px">
  <svg width="13" height="13" viewBox="0 0 14 14" style="margin-right:4px"><path d="M7 1.5c3.2 0 5.5 2 5.5 4.6S10.2 10.7 7 10.7c-.6 0-1.2-.1-1.7-.2L2.2 12l.9-2.5C2 8.6 1.5 7.4 1.5 6.1 1.5 3.5 3.8 1.5 7 1.5z" fill="none" stroke="#fff" stroke-width="1.3"/></svg>Live Chat</a>

</div>
</body>
</html>
```